RW Holloway LLC Business Card - Civil Engineering & Consulting Firm

We need a Business Card that is elegant, and masculine.  It is our Professional Civil Engineering & Consulting Company located in San Antonio TX (Not s construction or builder firm- no gears & no tool images please). We provide civil engineering services including  commercial site plans, grading and drainage plans, utility plans, hydraulics and hydrology, land planning, utility coordination, and other general civil engineering services related to commercial and residential development.
We have 2 existing Logos. We would like to convey reliability, strength, trustworthiness and attention to detail.  Blues and orange tones as per logo We are OK with the use of a darker blue in the mix.  We have 2 logo versions - Full Company Name Logo to go on the back of card, & Small Icon Logo for the front w/ personal Info.

Target Market(s)
Architects, Real Estate Developers, Other Strctural Engineers, Surveyers, General Contractors
Industry/Entity Type
Professional Civil Engineering
Contact Information for Business Card
Name, Position, Address, Cell & Office #, email, and company website
Font styles to use
Other font styles liked:
- Avian
Requirements
Should not have
- No Tools, No Gears, no Cranes, or Construction Equipment.

```html
<!DOCTYPE html>
<html lang="en">
<head>
<meta charset="UTF-8">
<title>RW Holloway LLC — Business Card</title>
<link rel="stylesheet" href="https://fonts.googleapis.com/css2?family=Montserrat:wght@300;400;500&family=Arimo:wght@400&display=swap">
<style>
  :root {
    --bg: #bdbdbd;
    --card-white: #ffffff;
    --brand-blue: #6fa3d8;
    --brand-orange: #ef8a2a;
    --ink: #1b1b1b;
    --back-blue: #7aaed9;
    --silver: #d4dbe3;
    --rule-blue: #7fb0e0;
  }
  * { margin: 0; padding: 0; box-sizing: border-box; }
  html, body { width: 1200px; height: 800px; overflow: hidden; }
  body {
    background: var(--bg);
    display: flex;
    align-items: center;
    justify-content: center;
    gap: 50px;
    font-family: "Arimo", Arial, sans-serif;
  }
  .card {
    position: relative;
    width: 540px;
    height: 309px;
    overflow: hidden;
  }
  .card--front { background: var(--card-white); }
  .card--back { background: var(--back-blue); }

  /* Front */
  .brand {
    position: absolute;
    top: 58px;
    right: 46px;
    display: flex;
    align-items: center;
    gap: 10px;
  }
  .brand__mark {
    width: 14px; height: 14px;
    background: var(--brand-blue);
  }
  .brand__name {
    font-family: "Montserrat", sans-serif;
    font-weight: 300;
    font-size: 30px;
    letter-spacing: 2px;
    color: var(--brand-blue);
  }
  .divider {
    position: absolute;
    left: 34px; right: 34px;
    top: 150px;
    height: 1px;
    background: var(--rule-blue);
  }
  .person {
    position: absolute;
    left: 34px;
    top: 168px;
  }
  .person__name {
    font-family: "Montserrat", sans-serif;
    font-weight: 400;
    font-size: 20px;
    letter-spacing: 0.5px;
  }
  .person__first { color: var(--brand-blue); }
  .person__last { color: var(--brand-orange); }
  .person__title {
    font-size: 14px;
    color: var(--ink);
    margin-top: 2px;
    padding-bottom: 8px;
    border-bottom: 1px solid var(--rule-blue);
    width: 230px;
  }
  .contact { list-style: none; margin-top: 8px; }
  .contact__item {
    display: flex; align-items: center; gap: 8px;
    font-size: 14px; color: var(--ink); line-height: 21px;
  }
  .contact__icon { width: 13px; height: 13px; flex: none; }
  .accent { color: var(--brand-orange); }
  .address {
    position: absolute;
    right: 40px;
    top: 176px;
    font-size: 14px;
    line-height: 20px;
    color: var(--ink);
    text-align: right;
  }

  /* Back */
  .back__brand {
    position: absolute;
    left: 0; right: 0;
    top: 110px;
    text-align: center;
    font-family: "Montserrat", sans-serif;
    font-weight: 300;
    font-size: 40px;
    letter-spacing: 3px;
    color: var(--silver);
  }
  .back__tagline {
    position: absolute;
    left: 0; right: 0;
    bottom: 48px;
    text-align: center;
    font-family: "Montserrat", sans-serif;
    font-weight: 400;
    font-size: 17px;
    letter-spacing: 0.6px;
    color: #ffffff;
  }
</style>
</head>
<body>
  <section class="card card--front" aria-label="Business card front">
    <div class="brand">
      <span class="brand__mark"></span>
      <span class="brand__name">RW Holloway LLC</span>
    </div>
    <div class="divider"></div>
    <div class="person">
      <p class="person__name"><span class="person__first">DANIEL</span> <span class="person__last">REYES</span></p>
      <p class="person__title">Managing Director</p>
      <ul class="contact">
        <li class="contact__item">
          <svg class="contact__icon" viewBox="0 0 16 16"><path fill="var(--brand-blue)" d="M3 1l3 3-1.5 2c1 2 3 4 5 5L11.5 9.5l3 3L12.5 15C6 14 2 10 1 3.5z"/></svg>
          044-210 555 318
        </li>
        <li class="contact__item">
          <svg class="contact__icon" viewBox="0 0 16 16"><rect x="1" y="3" width="14" height="10" fill="var(--brand-blue)"/><path d="M1 3l7 6 7-6" fill="none" stroke="#fff" stroke-width="1.2"/></svg>
          info@hollowayeng.com
        </li>
        <li class="contact__item">
          <svg class="contact__icon" viewBox="0 0 16 16"><circle cx="8" cy="8" r="7" fill="none" stroke="var(--brand-blue)" stroke-width="1.5"/><ellipse cx="8" cy="8" rx="3" ry="7" fill="none" stroke="var(--brand-blue)"/><path d="M1 8h14" stroke="var(--brand-blue)"/></svg>
          www.<span class="accent">hollowayeng</span>.com
        </li>
      </ul>
    </div>
    <address class="address" style="font-style:normal">421, Alamo Ridge Drive<br>78205, San Antonio TX</address>
  </section>

  <section class="card card--back" aria-label="Business card back">
    <p class="back__brand">RW Holloway LLC</p>
    <p class="back__tagline">Commercial and Residential Development</p>
  </section>
</body>
</html>
```